Larkspur Talent IT Recruiting firm needs a business card design for Recruiters, Sourcers, and Account

We need business cards that allow us to change all contact info, names, titles (Recruiter, Sourcer, Account Manager, Director, CEO, etc) per person since we have three offices, in three cities, Phoenix, Austin, and Las Vegas. We do recruiting and contractors for IT positions (Developers, Architects, Software Engineers, Security Engineers, Help Desk, DBAs, PMs, Scrum Masters, etc.) Our client companies are very diverse from Meridian 100 to silicone Valley type start-ups.

So, while we what hip, techie, and quirky, it still needs to be professional. Primary color we use is blue, with silver as a secondary color.

Target Market(s)

IT, Technology

Industry/Entity Type

Business

Contact Information for Business Card

Company name: Larkspur Talent, Inc.
Website: www.larkspurtalent.example
Logos for Careerloop, Blipster, and Myriada

Name, Title, Office Number, Cell Number, email

Font styles to use
Serif
Sans Serif

Colors
0455a3
d5d5d5

Requirements
Nice to have
• The grey I selected below is not necessary - but, would like silver included. I included a card design (File 3: LTI early trial example.jpg) that I had started on. It's very rough, and not quite what we're looking for, but what we did like is the logo, big, maybe a bit faded, off center, goes out of frame, etc. Still looking for other ideas - you are the pros! But, just an idea of a design element we liked.

```html
<!DOCTYPE html>
<html lang="en">
<head>
<meta charset="utf-8">
<title>Larkspur Talent – Business Card</title>
<link rel="stylesheet" href="https://fonts.googleapis.com/css2?family=Cinzel:wght@400;600&family=Open+Sans:wght@400;700&display=swap">
<style>
  :root {
    --backdrop: #3b3b3d;
    --card-black: #0b0b0c;
    --card-black-soft: #1c1c1e;
    --card-white: #ffffff;
    --brand-blue: #0455a3;
    --bright-blue: #1e8fdc;
    --silver: #d5d5d5;
    --ink: #2b2b2b;
    --ink-soft: #555555;
  }
  * { box-sizing: border-box; margin: 0; padding: 0; }
  html, body { width: 1200px; height: 852px; overflow: hidden; }
  body {
    background: var(--backdrop);
    font-family: "Open Sans", Arial, sans-serif;
    position: relative;
  }
  .card {
    position: absolute;
    width: 560px;
    height: 320px;
    border-radius: 14px;
    overflow: hidden;
  }
  /* Front side */
  .card-front {
    left: 27px; top: 266px;
    background: radial-gradient(ellipse at 60% 30%, var(--card-black-soft), var(--card-black) 70%);
  }
  .wordmark {
    position: absolute;
    left: 0; right: 0; top: 118px;
    display: flex; align-items: center; justify-content: center; gap: 14px;
  }
  .wordmark-dot {
    width: 40px; height: 40px; border-radius: 50%;
    background: var(--bright-blue);
    flex: none;
  }
  .wordmark-name {
    font-family: "Cinzel", Georgia, serif;
    font-weight: 600;
    font-size: 36px;
    letter-spacing: 2px;
    color: var(--card-white);
    white-space: nowrap;
  }
  .tagline {
    position: absolute;
    left: 0; right: 0; top: 196px;
    text-align: center;
    font-family: "Cinzel", Georgia, serif;
    font-size: 15px;
    letter-spacing: 2.5px;
    color: var(--silver);
  }
  /* Back side */
  .card-back {
    left: 613px; top: 266px;
    background: var(--card-white);
  }
  .brand-disc {
    position: absolute;
    left: 318px; top: 40px;
    width: 200px; height: 200px;
    border-radius: 50%;
    background: linear-gradient(160deg, var(--bright-blue), var(--brand-blue));
  }
  .person {
    position: absolute; left: 30px; top: 72px;
  }
  .person-name {
    font-weight: 700; font-size: 15px; letter-spacing: .5px;
    color: var(--bright-blue);
  }
  .person-title {
    font-size: 10px; color: var(--ink-soft); margin-top: 1px;
  }
  .contact-list {
    position: absolute; left: 30px; top: 132px;
    list-style: none;
  }
  .contact-list li {
    display: flex; align-items: center; gap: 10px;
    font-size: 12px; line-height: 19px; color: var(--ink);
  }
  .contact-list svg { width: 12px; height: 12px; fill: var(--brand-blue); flex: none; }
  .contact-list .address { padding-left: 22px; }
  .social-row {
    position: absolute; left: 30px; top: 262px;
    display: flex; gap: 12px;
  }
  .social-item {
    display: flex; align-items: center; gap: 5px;
    font-size: 10px; font-weight: 700; color: var(--bright-blue);
  }
  .social-item::before {
    content: ""; width: 12px; height: 12px; border-radius: 2px;
    background: var(--bright-blue);
  }
</style>
</head>
<body>
  <section class="card card-front" aria-label="Card front">
    <div class="wordmark">
      <span class="wordmark-dot"></span>
      <span class="wordmark-name">LARKSPUR TALENT</span>
    </div>
    <p class="tagline">BUILT FOR WHAT COMES NEXT</p>
  </section>

  <section class="card card-back" aria-label="Card back">
    <div class="brand-disc" aria-hidden="true"></div>
    <div class="person">
      <p class="person-name">DANA WHITCOMBE</p>
      <p class="person-title">CEO</p>
    </div>
    <ul class="contact-list">
      <li>
        <svg viewBox="0 0 12 12" aria-hidden="true"><path d="M2.5 1 4.5 1 5 3.5 3.8 4.5C4.5 6 6 7.5 7.5 8.2L8.5 7 11 7.5 11 9.5C11 10.3 10.3 11 9.5 11 5 11 1 7 1 2.5 1 1.7 1.7 1 2.5 1Z"/></svg>
        555| 010-2840
      </li>
      <li>
        <svg viewBox="0 0 12 12" aria-hidden="true"><path d="M3 1h6v3H3zM1 5h10v4H9v2H3V9H1zM4 8v2h4V8z"/></svg>
        555| 010-7316
      </li>
      <li>
        <svg viewBox="0 0 12 12" aria-hidden="true"><path d="M1 2.5h10v7H1zM1.8 3.2 6 6.5l4.2-3.3v.9L6 7.4 1.8 4.1z" fill-rule="evenodd"/></svg>
        dana@larkspurtalent.example
      </li>
      <li>
        <svg viewBox="0 0 12 12" aria-hidden="true"><circle cx="6" cy="6" r="5"/><path d="M1 6h10M6 1c2 2 2 8 0 10M6 1c-2 2-2 8 0 10" stroke="#fff" stroke-width=".7" fill="none"/></svg>
        www.larkspurtalent.example
      </li>
      <li class="address">2280 Alder Crest Ave, Suite 14</li>
      <li class="address">Mesa Verde, AZ 85000, USA</li>
    </ul>
    <div class="social-row">
      <span class="social-item">Blipster</span>
      <span class="social-item">Careerloop</span>
      <span class="social-item">Myriada</span>
    </div>
  </section>
</body>
</html>
```